Quorbelt

I have attached a doc file with the information for the brochure as well as a video, logos also.

Requirements
Must have
• It is a 8.5 x 11 foldable brochure.

```html
<!DOCTYPE html>
<html lang="en">
<head>
<meta charset="utf-8">
<title>Quorbelt Brochure</title>
<link href="https://fonts.googleapis.com/css2?family=Montserrat:wght@600;700;800&display=swap" rel="stylesheet">
<style>
  :root {
    --backdrop: #bdbebf;
    --paper: #ffffff;
    --ink: #111111;
    --night: #000000;
    --brand-red: #ab2426;
    --claim-red: #ad2e34;
    --claim-blue: #1177be;
    --claim-green: #066b39;
    --claim-purple: #9c1d62;
    --device-dark: #2b2b2b;
    --device-light: #e4e4e4;
  }
  * { margin: 0; padding: 0; box-sizing: border-box; }
  html, body {
    width: 1200px; height: 1000px; overflow: hidden;
    background: var(--backdrop);
    font-family: "Montserrat", Arial, sans-serif;
  }
  .brochure {
    position: absolute; left: 82px; top: 100px;
    width: 1036px; height: 800px;
    background: var(--paper); overflow: hidden;
  }
  .backdrop-shapes { position: absolute; inset: 0; }
  .claim-label {
    position: absolute; color: var(--paper); font-weight: 700;
    text-align: center; line-height: 1.25;
  }
  .claim-title { left: 0; top: 62px; width: 300px; font-size: 28px; line-height: 1.3; }
  .claim-mail { left: 310px; top: 100px; width: 170px; font-size: 16.5px; }
  .claim-ondemand { left: 220px; top: 243px; width: 160px; font-size: 16.5px; }
  .claim-store { left: 58px; top: 287px; width: 180px; font-size: 15.5px; line-height: 1.42; }

  .brand-name {
    position: absolute; left: 578px; top: 78px; width: 400px;
    display: flex; align-items: center; justify-content: center; gap: 16px;
    font-weight: 700; font-size: 60px; line-height: 1; color: var(--paper);
  }
  .brand-dot { width: 56px; height: 56px; border-radius: 50%; background: var(--brand-red); flex: none; }

  .coverage { position: absolute; left: 560px; top: 278px; width: 436px; text-align: center; }
  .coverage-heading { color: var(--brand-red); font-weight: 800; font-size: 26px; line-height: 1.15; }
  .coverage-list { color: var(--ink); font-weight: 700; font-size: 21px; line-height: 1.3; }

  .devices-visual {
    position: absolute; left: 603px; top: 398px; width: 350px; height: 332px;
  }
  .site-address {
    position: absolute; left: 660px; top: 764px; width: 230px; text-align: center;
    font-size: 11.5px; font-weight: 600; color: var(--ink);
  }

  .contact { position: absolute; left: 150px; top: 585px; width: 220px; text-align: center; }
  .contact-brand {
    display: inline-flex; align-items: center; gap: 8px;
    font-weight: 700; font-size: 22px; color: var(--brand-red);
  }
  .contact-brand-dot { width: 20px; height: 20px; border-radius: 50%; background: var(--brand-red); }
  .contact-heading {
    margin-top: 70px; font-weight: 800; font-size: 22px; color: var(--brand-red);
  }
  .contact-details { margin-top: 12px; font-size: 10.5px; font-weight: 600; line-height: 1.3; color: var(--ink); }
</style>
</head>
<body>
<main class="brochure">
  <svg class="backdrop-shapes" width="1036" height="800" viewBox="0 0 1036 800" aria-hidden="true">
    <path d="M0,0 H1036 V238 C700,246 390,314 226,448 C116,540 44,660 36,800 H0 Z" fill="var(--brand-red)"/>
    <path d="M0,0 H1036 V224 C700,230 360,296 200,425 C100,505 30,585 0,650 Z" fill="var(--night)"/>
    <path d="M1036,224 C700,230 360,296 200,425 C100,505 30,585 0,650" fill="none" stroke="var(--paper)" stroke-width="4"/>
    <g stroke="var(--paper)" stroke-width="2">
      <circle cx="403" cy="122" r="94" fill="var(--claim-blue)"/>
      <circle cx="300" cy="262" r="102" fill="var(--claim-green)"/>
      <circle cx="148" cy="345" r="102" fill="var(--claim-purple)"/>
      <circle cx="150" cy="115" r="152" fill="var(--claim-red)"/>
    </g>
  </svg>

  <p class="claim-label claim-title">3 Different ways<br>to file a claim</p>
  <p class="claim-label claim-mail">Mail-in service<br>(free shipping)</p>
  <p class="claim-label claim-ondemand">Quorbelt<br>On-Demand</p>
  <p class="claim-label claim-store">Reimbursement<br>at your<br>local store<br>or Fix Counter<br>(your choice)</p>

  <div class="brand-name"><span class="brand-dot"></span>Quorbelt</div>

  <section class="coverage">
    <h2 class="coverage-heading">WE COVER ALL</h2>
    <p class="coverage-list">smartphon • esorbpad's • orbphones<br>smart watches • tablets</p>
  </section>

  <svg class="devices-visual" role="img" aria-label="Monitor, tablet and phone showing the Quorbelt name" viewBox="0 0 350 332">
    <defs>
      <linearGradient id="device-tone" x1="0" y1="0" x2="0" y2="1">
        <stop offset="0" stop-color="var(--device-dark)"/>
        <stop offset="1" stop-color="var(--device-light)"/>
      </linearGradient>
    </defs>
    <rect width="350" height="332" rx="10" fill="url(#device-tone)"/>
  </svg>
  <p class="site-address">www.quorbelt.com</p>

  <section class="contact">
    <div class="contact-brand"><span class="contact-brand-dot"></span>Quorbelt</div>
    <h2 class="contact-heading">CONTACT US</h2>
    <p class="contact-details">phone: 001-5550-382<br>email: info@quorbelt.com<br>web: www.quorbelt.com</p>
  </section>
</main>
</body>
</html>
```